TK Stationery - Modern Contemporary

Develop modern template for Letterhead and Stationery (business card, letterhead, envelopes) using the TK Logo and Icon

Colors
0054AA
0677BA
7BADD7
CADEEF
E8F1F8
00AB8E
00BBA5
67D7C9
C6EFE9
E9F9F6
EE7325
F08F49
F5BC92
FAE3D3
FDF4ED
6B429C
8869AF
B7A5CE
E3DAEB
F3F0F8

```html
<!DOCTYPE html>
<html lang="en">
<head>
<meta charset="utf-8">
<title>Tala Kinsey Letterhead</title>
<link rel="stylesheet" href="https://fonts.googleapis.com/css2?family=Lora:wght@500&family=Questrial&family=Arimo:wght@400;700&display=swap">
<style>
  :root {
    --navy: #29304b;
    --green: #3aae73;
    --orange: #ef8433;
    --ink: #505050;
    --backdrop: #e9e9ea;
    --paper: #ffffff;
  }
  * { margin: 0; padding: 0; box-sizing: border-box; }
  html, body { width: 1173px; height: 1200px; overflow: hidden; background: var(--backdrop); }
  .letterhead {
    position: absolute; left: 230px; top: 95px;
    width: 714px; height: 1010px;
    background: var(--paper); overflow: hidden;
  }
  .brand-name {
    position: absolute; top: 46px; left: 0; width: 100%;
    text-align: center;
    font-family: "Lora", serif; font-weight: 500;
    font-size: 36px; color: var(--navy); letter-spacing: 0.5px;
  }
  .greeting {
    position: absolute; left: 65px; top: 310px;
    font-family: "Questrial", sans-serif; font-size: 16px; font-weight: 700;
    color: var(--ink);
  }
  .letter-body {
    position: absolute; left: 63px; top: 357px; width: 584px;
    font-family: "Arimo", sans-serif; font-size: 11.4px; line-height: 14.8px;
    color: var(--ink); text-align: justify;
  }
  .letter-body p { margin-bottom: 12.6px; }
  .closing {
    position: absolute; left: 65px; top: 660px;
    font-family: "Questrial", sans-serif; font-size: 9px; font-weight: 700; color: var(--ink);
  }
  .signature {
    position: absolute; left: 64px; top: 704px; width: 117px; height: 35px;
    background: linear-gradient(90deg, #6a6a6a, #8a8a8a); opacity: 0.35; border-radius: 4px;
  }
  .footer-art { position: absolute; left: 0; top: 0; }
  .contact-list {
    position: absolute; left: 403px; top: 943px; list-style: none;
    font-family: "Arimo", sans-serif; font-size: 11px; line-height: 14.5px; color: #fff;
  }
  .contact-list li { display: flex; align-items: center; gap: 6px; }
  .contact-list svg { width: 9px; height: 9px; flex: none; }
  .footer-divider {
    position: absolute; left: 554px; top: 946px; width: 1px; height: 38px; background: #fff;
  }
  .address {
    position: absolute; left: 569px; top: 943px;
    font-family: "Arimo", sans-serif; font-size: 11px; line-height: 14.5px; color: #fff;
  }
</style>
</head>
<body>
<main class="letterhead">
  <svg class="footer-art" width="714" height="1010" viewBox="0 0 714 1010" aria-hidden="true">
    <rect x="0" y="927" width="714" height="8" fill="var(--green)"/>
    <rect x="0" y="934" width="714" height="76" fill="var(--navy)"/>
    <circle cx="50" cy="960" r="94" fill="var(--paper)"/>
    <circle cx="50" cy="960" r="80" fill="var(--orange)"/>
  </svg>

  <h1 class="brand-name">tala kinsey</h1>

  <p class="greeting">Dear Mr. Smith,</p>

  <div class="letter-body">
    <p>Lorem ipsum dolor sit amet, consectetuer adipiscing elit, sed diam nonmmy nibh euismod tincidunt ut laor eet dolore magna aliquam erat volutpat. Ut wisi enim ad minim veniam, quis nostrud exerci tationmcorper suscipit lobortis nisl ut aliquip ex ea commodo consequat. Duis autem vel eum iriure dolor in hendrerit in vulputate velit esse molestie consequat, vel illum dolore eu feugiat</p>
    <p>Rorem ipsum dolor sit amet, consectetuer adipiscing elit, sed diam nonmmy nibh euismod tincidunt ut laor eet dolore magna aliquam erat volutpat. Ut wisi enim ad minim veniam, quis nostrud exerci tationmcorper suscipit lobortis nisl ut aliquip ex ea commodo consequat. Duis autem vel eum iriure dolor in hendrerit in vulputate velit esse molest</p>
    <p>Dorem ipsum dolor sit amet, consectetuer adipiscing elit, sed diam nonmmy nibh euismod tincidunt ut laor eet dolore magna aliquam erat volutpat. Ut wisi enim ad minim veniam, quis nostrud exerci tationmcorper suscipit lobortis nisl ut aliquip ex ea commodo consequat. Duis autem vel eum iriure dolor in hendrerit in suscipit lobortis nisl ut aliquip ex ea commodo consequat. Duis autem vel eum iriure dolor in hendrerit in vulputate velit esse molestie consequat, vel illum</p>
    <p>Sorem ipsum dolor sit amet, consectetuer adipiscing elit, sed diam nonmmy nibh euismod tincidunt ut laor eet dolore magna aliquam erat volutpat. Ut wisi enim ad minim veniam, quis nostrud exerci tationmcorper suscipit lobortis nisl ut aliquip ex ea commodo consequat. Duis autem vel eum iriure dolor in</p>
  </div>

  <p class="closing">Sincerely,</p>
  <div class="signature" role="img" aria-label="Handwritten signature of the sender"></div>

  <ul class="contact-list">
    <li>
      <svg viewBox="0 0 10 10"><path d="M2 1 L4 1 L4.6 3 L3.4 3.8 Q4.4 5.8 6.2 6.6 L7 5.4 L9 6 L9 8 Q9 9 8 9 Q1 8.5 1 2 Q1 1 2 1Z" fill="var(--green)"/></svg>
      123-456-2100
    </li>
    <li>
      <svg viewBox="0 0 10 10"><rect x="0.5" y="2" width="9" height="6" fill="var(--green)"/><path d="M0.5 2 L5 5.5 L9.5 2" stroke="var(--navy)" stroke-width="0.9" fill="none"/></svg>
      info@talakinsey.com
    </li>
    <li>
      <svg viewBox="0 0 10 10"><circle cx="5" cy="5" r="4.3" fill="none" stroke="var(--green)" stroke-width="1.3"/><circle cx="5" cy="5" r="2" fill="var(--green)"/></svg>
      www.talakinsey.com
    </li>
  </ul>
  <div class="footer-divider"></div>
  <address class="address" style="font-style:normal">
    Your address<br>city<br>state, ZIP 0000
  </address>
</main>
</body>
</html>
```